SnackOrbit!!! A Vending Machine Business Looking for an attractive website.

We are a vending machine business in Northern Michigan. We have changed our name and have rebranded our company. We would like an attractive website that shares who we are, what services we provide, the products we offer in our machines, along with a form businesses can fill out to see if they are a good fit for our company. I would like to have a Home Page, About SnackOrbit, Why Choose SnackOrbit?, Products & Services, Contact Us (With a Login Option), and a page with a questionnaire for thos interested in getting a FREE Vending Machine.

Target Market(s)

Businesses, Campgrounds, Schools, and many more in Northern Michigan

Industry/Entity Type

Vending Machines

Coding

Coded - Design and coding required

Number of Pages Required

5+ page

Requirements
Must have
• An inviting and enticing Home Page. I want to get my potential clients engaged in our website.
Nice to have
• Possibly background photos from Northern Michigan
Should not have
• A corporate feel. I do not want a boring website.

```html
<!DOCTYPE html>
<html lang="en">
<head>
<meta charset="utf-8">
<title>SnackOrbit – Vending Machines in Northern Michigan</title>
<link rel="stylesheet" href="https://fonts.googleapis.com/css2?family=Outfit:wght@300;400;500;600;700&family=Lilita+One&display=swap">
<style>
:root{
  --navy:#1e1f5c;
  --navy-deep:#17184a;
  --green:#2f5a2a;
  --white:#ffffff;
  --ink:#1f1f2a;
  --muted:#55556a;
  --paper:#f3f2f4;
  --line:#1e1f5c;
}
*{box-sizing:border-box;margin:0;padding:0}
html,body{width:1200px;height:4402px;overflow:hidden}
body{font-family:'Outfit',sans-serif;color:var(--ink);background:var(--white);position:relative}
section,header,footer,.topbar{position:absolute;left:0;width:1200px}
.abs{position:absolute}
.btn{position:absolute;display:flex;align-items:center;justify-content:center;background:var(--green);color:var(--white);font-weight:700;text-transform:uppercase;letter-spacing:.3px}

/* top bar */
.topbar{top:0;height:43px;background:var(--navy);color:var(--white);font-size:13px}
.topbar .follow{left:137px;top:0;height:43px;display:flex;align-items:center;gap:8px}
.topbar .dot{width:17px;height:17px;border-radius:50%;background:var(--white)}
.topbar .phone{left:578px;top:0;height:43px;display:flex;align-items:center;gap:8px;padding-left:20px;border-left:1px solid rgba(255,255,255,.35)}
.topbar .free{left:750px;top:0;height:43px;display:flex;align-items:center;padding:0 22px;border-left:1px solid rgba(255,255,255,.35)}
.topbar .login{left:983px;top:0;width:85px;height:43px;background:var(--green);display:flex;align-items:center;justify-content:center}

/* header */
header{top:43px;height:121px;background:var(--white)}
.logo{left:133px;top:32px;font-weight:700;font-size:40px;color:var(--navy);display:flex;align-items:center;gap:10px}
.logo .mark{width:14px;height:44px;background:var(--green)}
.nav{left:415px;top:43px;display:flex;align-items:center;font-size:14.5px;color:var(--ink)}
.nav a{color:inherit;text-decoration:none;margin-right:22px}
.nav a.active{background:var(--green);color:var(--white);padding:10px 13px}

/* hero */
.hero{top:164px;height:550px;background:linear-gradient(180deg,#4a5a72 0%,#3b4a3a 55%,#5a4f3e 100%)}
.hero-photo{left:0;top:0;width:1200px;height:550px}
.hero h1{left:679px;top:92px;font-family:'Lilita One',sans-serif;font-weight:400;font-size:58px;line-height:66px;color:var(--white);letter-spacing:.5px}
.hero .sub{left:681px;top:310px;font-size:20px;font-weight:500;color:var(--white)}
.hero .btn{left:684px;top:369px;width:299px;height:50px;background:var(--white);color:var(--navy);font-family:'Lilita One',sans-serif;font-weight:400;font-size:17px}
.arrow{position:absolute}

/* who */
.who{top:714px;height:472px}
h2.title{position:absolute;font-weight:700;font-size:28px;color:var(--navy);text-transform:uppercase}
.rule{position:absolute;width:70px;height:2px;background:var(--navy)}
.who p{left:133px;top:158px;width:370px;font-size:14px;line-height:19.3px;color:var(--ink)}
.who .btn{left:133px;top:344px;width:118px;height:41px;font-family:'Lilita One',sans-serif;font-weight:400;font-size:14px}

/* services */
.services{top:1186px;height:562px;background:var(--navy)}
.services .img{left:0;top:0;width:667px;height:562px;background:linear-gradient(135deg,#2a1c14 0%,#5b3b22 40%,#1b1a22 100%)}
.service{position:absolute;left:690px;width:510px}
.service svg{position:absolute;left:20px}
.service h3{position:absolute;left:93px;font-size:13.5px;font-weight:500;color:var(--white);text-transform:uppercase}
.service p{position:absolute;left:95px;top:22px;width:290px;font-size:13px;line-height:19px;color:#d8d8ea;font-weight:300}
.srule{position:absolute;left:690px;width:510px;height:2px;background:rgba(255,255,255,.85)}

/* why */
.why{top:1748px;height:523px}
.feature{position:absolute;top:218px;width:240px;text-align:center}
.feature .badge{margin:0 auto;width:146px;height:146px;border-radius:50%;background:var(--green);display:flex;align-items:center;justify-content:center}
.feature .inner{width:128px;height:128px;border-radius:50%;border:2px solid var(--white);display:flex;align-items:center;justify-content:center}
.feature span{display:block;margin-top:22px;font-size:13.5px;line-height:23px;text-transform:uppercase;color:var(--ink)}
.vline{position:absolute;top:209px;width:2px;height:222px;background:var(--navy)}

/* products */
.products{top:2271px;height:730px;background:var(--paper)}
.product{position:absolute;top:199px;width:230px;text-align:center}
.product .photo{margin:0 auto;width:140px;height:264px;background:linear-gradient(180deg,#3a3a44,#9a9aa4)}
.product h4{margin-top:50px;font-size:14px;font-weight:500;text-transform:uppercase}
.product p{margin-top:14px;font-size:12px;line-height:17.5px;color:var(--muted)}
.product .btn{position:relative;margin:18px auto 0;width:94px;height:30px;font-size:11px}

/* cta */
.cta{top:3001px;height:436px;background:var(--navy);text-align:center;color:var(--white)}
.cta h2{position:absolute;left:0;width:1200px;top:73px;font-size:35px;line-height:51px;font-weight:700;text-transform:uppercase}
.cta p{position:absolute;left:0;width:1200px;top:201px;font-size:19px;line-height:34px;font-weight:300}
.cta .btn{left:518px;top:294px;width:164px;height:51px;font-size:17px}

/* quote */
.quote{top:3437px;height:600px;background:linear-gradient(90deg,#1c1d22 0%,#2b2d33 45%,#3a3324 75%,#1c1a18 100%)}
.quote h2{color:var(--white);left:126px;top:60px}
.quote .rule{background:var(--white);left:131px;top:123px;width:55px}
.field{position:absolute;background:var(--white);font-size:11.5px;color:#555;padding:12px 11px}
.quote .btn{left:132px;top:480px;width:114px;height:50px;font-size:17px}

/* footer */
footer{top:4037px;height:365px;background:var(--white)}
.flogo{left:133px;top:120px;font-weight:700;font-size:44px;color:var(--navy);display:flex;align-items:center;gap:10px}
.flogo .mark{width:14px;height:50px;background:var(--green)}
.fcol h5{position:absolute;font-size:13px;font-weight:600;color:var(--ink)}
.fline{position:absolute;height:2px;background:var(--navy)}
.fitem{position:absolute;display:flex;align-items:center;gap:12px;font-size:11.5px;line-height:15px;color:var(--ink)}
.fitem .ic{width:22px;height:22px;border-radius:50%;background:var(--ink);display:flex;align-items:center;justify-content:center;flex:none}
.fmenu{position:absolute;left:747px;top:98px;font-size:11.5px;line-height:19.3px}
.bottomline{left:133px;top:283px;width:935px;height:1px;background:var(--navy)}
.copy{left:0;width:1200px;top:316px;text-align:center;font-size:10.5px}
</style>
</head>
<body>

<div class="topbar">
  <div class="abs follow">Follow us <span class="dot"></span><span class="dot"></span><span class="dot"></span></div>
  <div class="abs phone">
    <svg width="15" height="15" viewBox="0 0 24 24" fill="none" stroke="#fff" stroke-width="2"><path d="M22 16.9v3a2 2 0 0 1-2.2 2 19.8 19.8 0 0 1-8.6-3.1 19.5 19.5 0 0 1-6-6A19.8 19.8 0 0 1 2.1 4.2 2 2 0 0 1 4.1 2h3a2 2 0 0 1 2 1.7c.1 1 .4 1.9.7 2.8a2 2 0 0 1-.5 2.1L8 9.9a16 16 0 0 0 6 6l1.3-1.3a2 2 0 0 1 2.1-.4c.9.3 1.8.6 2.8.7a2 2 0 0 1 1.7 2z"/></svg>
    +1 231 555 0142
  </div>
  <div class="abs free">Get a FREE Vending Machine</div>
  <div class="abs login">Login</div>
</div>

<header>
  <div class="abs logo"><span class="mark"></span>SnackOrbit</div>
  <nav class="abs nav">
    <a class="active">Home</a><a>About SnackOrbit</a><a>Why Choose SnackOrbit?</a><a>Products &amp; Services</a><a>Contact Us</a>
  </nav>
</header>

<section class="hero">
  <div class="abs hero-photo" role="img" aria-label="Two vending machines over an aerial view of a Northern Michigan lakeside town"></div>
  <h1 class="abs">SNACKORBIT<br>ELEVATE YOUR<br>SNACK GAME!</h1>
  <div class="abs sub">Elevating Snacking, One Vend at a Time</div>
  <div class="btn">GET A FREE VENDING MACHINE</div>
  <svg class="arrow" style="left:52px;top:424px" width="30" height="50" viewBox="0 0 30 50"><path d="M25 3 5 25l20 22" fill="none" stroke="#fff" stroke-width="3"/></svg>
  <svg class="arrow" style="left:1122px;top:424px" width="30" height="50" viewBox="0 0 30 50"><path d="M5 3l20 22L5 47" fill="none" stroke="#fff" stroke-width="3"/></svg>
</section>

<section class="who">
  <h2 class="title" style="left:133px;top:62px">Who We Are</h2>
  <div class="rule" style="left:133px;top:116px"></div>
  <p class="abs">Welcome to SnackOrbit, where snacking meets delight! We're not just about vending machines; we're your culinary companions, your flavor curators, and your secret stash of happiness. Marcus and Elena, the dynamic duo behind SnackOrbit, have a passion for all things tasty. With backgrounds in sales and a penchant for personal connections, they've transformed the vending experience into an art form.</p>
  <div class="btn">Read More</div>
  <svg class="abs" style="left:528px;top:0" width="560" height="472" viewBox="0 0 560 472">
    <circle cx="139" cy="234" r="137" fill="#6f7a80" role="img" aria-label="Vending machine in a bright lobby"/>
    <circle cx="386" cy="231" r="154" fill="#b0652e" role="img" aria-label="Autumn forest hills of Northern Michigan"/>
  </svg>
</section>

<section class="services">
  <div class="abs img" role="img" aria-label="Row of lit vending machines stocked with snacks in a dark room"></div>
  <h2 class="title" style="left:690px;top:50px;color:#fff">Our Services</h2>
  <div class="service" style="top:1347px;top:161px">
    <svg style="top:-6px" width="50" height="50" viewBox="0 0 50 50" fill="none" stroke="#fff" stroke-width="2"><path d="M8 30l10-10 8 4 8-8 8 10-12 12-8-2-6 4z"/><path d="M25 4v6M15 8l3 5M35 8l-3 5"/></svg>
    <h3>Technical Support</h3>
    <p>Lorem Ipsum is simply dummy text of the prin ting and typesetting industry. Lorem Ipsum has been the industry'</p>
  </div>
  <div class="srule" style="top:262px"></div>
  <div class="service" style="top:294px">
    <svg style="top:4px" width="50" height="52" viewBox="0 0 50 52" fill="none" stroke="#fff" stroke-width="2"><rect x="10" y="2" width="30" height="48" rx="2"/><rect x="14" y="8" width="16" height="26"/><path d="M34 10v8M14 42h22"/></svg>
    <h3>Sleek &amp; Modern Machines</h3>
    <p>Lorem Ipsum is simply dummy text of the prin ting and typesetting industry. Lorem Ipsum has been the industry'</p>
  </div>
  <div class="srule" style="top:395px"></div>
  <div class="service" style="top:438px">
    <svg style="top:-4px" width="50" height="52" viewBox="0 0 50 52" fill="none" stroke="#fff" stroke-width="2"><circle cx="25" cy="20" r="15"/><path d="M25 12l3 6 6 1-4 4 1 6-6-3-6 3 1-6-4-4 6-1z"/><path d="M15 32l-4 16 7-4 4 6M35 32l4 16-7-4-4 6"/></svg>
    <h3>Best Machines</h3>
    <p>Lorem Ipsum is simply dummy text of the prin ting and typesetting industry. Lorem Ipsum has been the industry'</p>
  </div>
</section>

<section class="why">
  <h2 class="title" style="left:0;width:1200px;text-align:center;top:62px">Why Choose SnackOrbit?</h2>
  <div class="rule" style="left:565px;top:134px"></div>
  <div class="feature" style="left:88px">
    <div class="badge"><div class="inner"><svg width="52" height="46" viewBox="0 0 52 46" fill="none" stroke="#fff" stroke-width="3"><path d="M26 42 6 22A11 11 0 0 1 26 8a11 11 0 0 1 20 14z"/></svg></div></div>
    <span>Local Love</span>
  </div>
  <div class="vline" style="left:325px"></div>
  <div class="feature" style="left:329px">
    <div class="badge"><div class="inner"><svg width="54" height="46" viewBox="0 0 54 46" fill="none" stroke="#fff" stroke-width="2"><path d="M4 20l10-10 10 4 6-4 10 2 10 10-16 16-8-4-6 4z"/><path d="M27 4v5M19 6l2 4M35 6l-2 4"/></svg></div></div>
    <span>Unleash Your<br>Cravings</span>
  </div>
  <div class="vline" style="left:590px"></div>
  <div class="feature" style="left:596px">
    <div class="badge"><div class="inner"><svg width="50" height="54" viewBox="0 0 50 54" fill="none" stroke="#fff" stroke-width="2"><circle cx="25" cy="20" r="15"/><path d="M18 20l5 5 9-9"/><path d="M15 32l-4 16 7-4 4 6M35 32l4 16-7-4-4 6"/></svg></div></div>
    <span>Quality Meets<br>Convenience</span>
  </div>
  <div class="vline" style="left:855px"></div>
  <div class="feature" style="left:873px">
    <div class="badge"><div class="inner"><svg width="44" height="54" viewBox="0 0 44 54" fill="none" stroke="#fff" stroke-width="2"><rect x="6" y="2" width="32" height="50" rx="2"/><rect x="10" y="8" width="18" height="28"/><path d="M32 10v10M10 44h24"/></svg></div></div>
    <span>Pandemic-Proof &amp;<br>Recession-Ready</span>
  </div>
</section>

<section class="products">
  <h2 class="title" style="left:0;width:1200px;text-align:center;top:53px">Our Products</h2>
  <div class="rule" style="left:565px;top:122px"></div>
  <svg class="arrow" style="left:62px;top:296px" width="30" height="56" viewBox="0 0 30 56"><path d="M27 2 3 28l24 26" fill="none" stroke="#a8a8b4" stroke-width="2"/></svg>
  <svg class="arrow" style="left:1120px;top:296px" width="30" height="56" viewBox="0 0 30 56"><path d="M3 2l24 26L3 54" fill="none" stroke="#a8a8b4" stroke-width="2"/></svg>
  <div class="product" style="left:105px">
    <div class="photo" role="img" aria-label="Black vending machine with orange trim"></div>
    <h4>Machine 1</h4>
    <p>Sed ut perspiciatis unde omnis<br>iste natus error sit voluptatem<br>accusantium doloremque<br>laudantium totam.</p>
    <div class="btn">Read More</div>
  </div>
  <div class="product" style="left:346px">
    <div class="photo" style="width:180px;background:linear-gradient(180deg,#b8b8bc,#c33)" role="img" aria-label="Red and white drinks and snack vending machine"></div>
    <h4>Machine 2</h4>
    <p>Sed ut perspiciatis unde omnis<br>iste natus error sit voluptatem<br>accusantium doloremque<br>laudantium totam.</p>
    <div class="btn">Read More</div>
  </div>
  <div class="product" style="left:606px">
    <div class="photo" style="width:150px;background:linear-gradient(180deg,#222,#555)" role="img" aria-label="Black snack vending machine with colourful rows"></div>
    <h4>Machine 3</h4>
    <p>Sed ut perspiciatis unde omnis<br>iste natus error sit voluptatem<br>accusantium doloremque<br>laudantium totam.</p>
    <div class="btn">Read More</div>
  </div>
  <div class="product" style="left:866px">
    <div class="photo" style="width:160px;background:linear-gradient(180deg,#6b5a74,#8a8a90)" role="img" aria-label="Silver snack vending machine with glass front"></div>
    <h4>Machine 4</h4>
    <p>Sed ut perspiciatis unde omnis<br>iste natus error sit voluptatem<br>accusantium doloremque<br>laudantium totam.</p>
    <div class="btn">Read More</div>
  </div>
</section>

<section class="cta">
  <h2>Ready to Experience<br>The SnackOrbit Difference?</h2>
  <p>Sign up now and let's connect. Taste the future of snacking firsthand!<br>Contact us todayand explore how our vending magic can elevate your space.</p>
  <div class="btn">Contact Us</div>
</section>

<section class="quote" role="img" aria-label="Close-up of a lit vending machine stocked with snacks">
  <h2 class="title">Get a Quote</h2>
  <div class="rule"></div>
  <div class="field" style="left:132px;top:162px;width:242px;height:41px">First Name</div>
  <div class="field" style="left:390px;top:162px;width:244px;height:41px">Last Name</div>
  <div class="field" style="left:132px;top:219px;width:242px;height:41px">Email id</div>
  <div class="field" style="left:390px;top:219px;width:244px;height:41px">Phone</div>
  <div class="field" style="left:132px;top:275px;width:502px;height:41px">Subject</div>
  <div class="field" style="left:132px;top:331px;width:502px;height:123px">Message</div>
  <div class="btn">Submit</div>
</section>

<footer>
  <div class="abs flogo"><span class="mark"></span>SnackOrbit</div>

  <div class="fcol">
    <h5 style="left:456px;top:51px">CONTACT US</h5>
    <div class="fline" style="left:456px;top:75px;width:193px"></div>
    <div class="fitem" style="left:456px;top:105px"><span class="ic"><svg width="10" height="12" viewBox="0 0 10 12"><path d="M5 0a4 4 0 0 0-4 4c0 3 4 8 4 8s4-5 4-8a4 4 0 0 0-4-4z" fill="#fff"/></svg></span>418 Birchwood Lane,<br>Petoskey MI</div>
    <div class="fitem" style="left:456px;top:155px"><span class="ic"><svg width="10" height="10" viewBox="0 0 24 24"><path d="M22 17v4a2 2 0 0 1-2 2C10 23 1 14 1 4a2 2 0 0 1 2-2h4l2 5-3 2a14 14 0 0 0 8 8l2-3 5 2z" fill="#fff"/></svg></span>Call Us<br>+1 231 555 0142</div>
    <div class="fitem" style="left:456px;top:207px"><span class="ic"><svg width="11" height="8" viewBox="0 0 11 8"><rect width="11" height="8" fill="#fff"/><path d="M0 0l5.5 4L11 0" fill="none" stroke="#1f1f2a"/></svg></span>E mail Us<br>info@snackorbit.com</div>
  </div>

  <div class="fcol">
    <h5 style="left:747px;top:51px">MENU</h5>
    <div class="fline" style="left:747px;top:75px;width:106px"></div>
    <div class="fmenu">Home<br>About SnackOrbit<br>Why Choose SnackOrbit?<br>Products &amp; Services<br>Contact Us</div>
  </div>

  <div class="fcol">
    <h5 style="left:960px;top:51px">FOLLOW US</h5>
    <div class="fline" style="left:960px;top:75px;width:108px"></div>
    <div class="fitem" style="left:960px;top:110px"><span class="ic"></span>Like us on<br>SNAPBOOK</div>
    <div class="fitem" style="left:960px;top:160px"><span class="ic"></span>Follow us on<br>WORKLINK</div>
    <div class="fitem" style="left:960px;top:212px"><span class="ic"></span>Follow us on<br>PICTOGRAM</div>
  </div>

  <div class="abs bottomline"></div>
  <div class="abs copy">Copyright © 2024 All Rights Reserved</div>
</footer>

</body>
</html>
```